Web Page Design for Major Airline Consolidator

We need a new design for an airline consolidator based out of NY. We'd really like to get the design as quickly as possible.

Here is a *very* rough mockup of what the site could look like, along with 3 main competitor's sites. Needless to say, they want a design that looks much better than their competitors. Please note that the mockup is an idea only, feel free to enhance / improve upon it.

Mockup - https://plankrafe.com/tvorel/KQPMzaLu

Competitors:
- http://www.brellintour.com/
- http://www.skorvatix.com/home2.html
- https://www.dulmerok.com/index.php

Target Market(s)

target markets are identified in the mockup

Industry/Entity Type

Airline

Number of Pages Required

1 page

Requirements
Must have
• need space on the left side for a travel request form which is missing in the mockup. Form should have standard air booking fields (to, from, date arrival & departure, travel class, etc).

```html
<!DOCTYPE html>
<html lang="en">
<head>
<meta charset="utf-8">
<title>Tarnwick Tours – Airline Consolidator</title>
<link href="https://fonts.googleapis.com/css2?family=Open+Sans:ital,wght@0,400;0,600;0,700;1,400&display=swap" rel="stylesheet">
<style>
:root{
  --red:#e04545;
  --red-dark:#c93434;
  --blue:#2f6fb5;
  --ink:#222;
  --muted:#555;
  --grey:#eeeff1;
  --grey-2:#e4e6e8;
  --line:#d9d9d9;
  --white:#fff;
  --sky-1:#6f9fcf;
  --sky-2:#c7dcef;
}
*{box-sizing:border-box;margin:0;padding:0}
html,body{width:1200px;height:3221px;overflow:hidden}
body{font-family:"Open Sans",Arial,sans-serif;color:var(--ink);background:var(--white);position:relative}
.abs{position:absolute}
.btn{position:absolute;background:var(--red);color:var(--white);font-weight:600;text-align:center;display:flex;align-items:center;justify-content:center;text-transform:uppercase}
.center{text-align:center}

/* header */
.site-header{left:80px;top:0;width:1040px;height:122px;background:var(--white)}
.brand{left:28px;top:6px;display:flex;align-items:center;gap:10px}
.brand-mark{width:44px;height:44px;background:var(--muted);border-radius:50%}
.brand-name{font-size:30px;font-weight:700;color:var(--muted);line-height:1}
.brand-tag{font-size:11px;color:var(--muted);margin-top:3px}
.social-top{right:40px;top:12px;display:flex;gap:22px}
.social-top span{width:14px;height:14px;border-radius:50%;background:#9aa0a6}
.search-top{right:30px;top:38px;width:210px;height:22px;background:#e9eaec;border-radius:11px}
.account{right:30px;top:74px;font-size:11px;color:var(--muted);display:flex;gap:14px}
.main-nav{left:28px;top:104px;display:flex;gap:26px;font-size:12px;color:var(--blue);text-transform:uppercase}
.main-nav .active{color:var(--red);border-bottom:2px solid var(--red);padding-bottom:2px}

/* hero */
.hero-photo{left:0;top:0;width:1200px;height:692px;background:linear-gradient(180deg,#3f6d9f 0%,var(--sky-1) 35%,var(--sky-2) 75%,#e6eef5 100%)}
.hero-arrow{top:325px;width:54px;height:58px;background:var(--red);display:flex;align-items:center;justify-content:center}
.tagline{left:107px;top:200px;width:618px;height:110px;background:rgba(200,215,232,.75);text-align:center;padding-top:12px}
.tagline h1{font-size:28px;font-weight:400;color:var(--white);letter-spacing:.5px}
.tagline .stars{color:var(--white);font-size:15px;margin-top:2px;letter-spacing:2px}
.tagline a{color:var(--white);font-size:14px;text-decoration:underline}
.access{left:751px;top:204px;width:357px;height:200px;background:var(--red);padding:18px 20px}
.access .field{height:38px;background:#f07b7b;color:var(--white);font-size:14px;display:flex;align-items:center;justify-content:center;margin-bottom:14px}
.access .go{position:absolute;left:67px;top:142px;width:220px;height:40px;background:#5a5a5a;color:var(--white);font-size:16px;display:flex;align-items:center;justify-content:center}

/* flight search */
.flight-search{left:80px;top:437px;width:1034px;height:255px;background:rgba(225,235,246,.78)}
.flight-search h2{position:absolute;left:0;width:100%;top:40px;text-align:center;font-size:18px;font-weight:600;color:var(--ink);margin-top:-8px}
.fs-input{position:absolute;height:34px;background:var(--white);border:1px solid #c9d3dd;font-size:13px;color:#777;display:flex;align-items:center;padding-left:10px}
.fs-input .caret{position:absolute;right:8px;top:13px;width:0;height:0;border-left:5px solid transparent;border-right:5px solid transparent;border-top:6px solid #777}
.fs-input .cal{position:absolute;right:8px;top:10px;width:14px;height:13px;border:2px solid #777;border-top-width:4px}
.opt{position:absolute;font-size:13px;color:var(--ink);display:flex;align-items:center;gap:6px}
.opt i{width:13px;height:13px;border-radius:50%;background:var(--white);border:1px solid #888;display:inline-block}
.opt i.on{background:var(--blue);border-color:var(--blue)}
.fs-note{position:absolute;font-size:13px;color:var(--ink)}

/* agents */
.section-title{position:absolute;left:0;width:1200px;text-align:center;font-size:21px;text-transform:uppercase;color:var(--ink)}
.agent{position:absolute;width:300px;text-align:center}
.agent .icon{width:100px;height:100px;margin:0 auto;border:2px dashed var(--blue);border-radius:50%;display:flex;align-items:center;justify-content:center}
.agent h3{font-size:17px;font-weight:400;color:var(--blue);text-transform:uppercase;margin-top:24px}
.agent .lead{font-size:14px;color:var(--muted);margin-top:6px}
.agent ul{list-style:none;font-size:13px;color:var(--ink);margin-top:10px;line-height:26px}
.agent .more{font-size:13px;color:var(--muted);margin-top:2px}
.divider{position:absolute;left:160px;width:880px;height:1px;background:linear-gradient(90deg,transparent,#e6b3b3,transparent)}
.badge{position:absolute;top:1272px;width:140px;height:66px;background:#cfd1d3;border-radius:6px}

/* corporate */
.corporate{left:0;top:1436px;width:1200px;height:357px;background:var(--grey)}
.corporate h2{position:absolute;left:280px;top:44px;font-size:20px;font-weight:400;text-transform:uppercase}
.corporate .sub{position:absolute;left:360px;top:83px;font-size:15px;color:var(--red);text-transform:uppercase}
.point{position:absolute;left:140px;display:flex;align-items:center;gap:14px;font-size:17px}
.point b{width:32px;height:32px;border-radius:50%;background:var(--red);color:var(--white);font-size:15px;display:flex;align-items:center;justify-content:center}
.agent-photo{left:880px;top:1490px;width:240px;height:303px;background:linear-gradient(160deg,#f1e6cf,#e4d2b0 50%,#c7cfd8);border-radius:120px 120px 0 0}

/* group travel */
.photo{position:absolute;top:1903px;width:440px;height:272px}
.group{position:absolute;width:440px;text-align:center}
.group h3{font-size:17px;font-weight:600;text-transform:uppercase}
.group p{font-size:14px;color:var(--muted);margin-top:10px;line-height:20px;padding:0 40px}

/* quote */
.quote{left:0;top:2375px;width:1200px;height:412px;background:var(--grey-2)}
.ceo-photo{left:60px;top:2380px;width:300px;height:407px;background:linear-gradient(180deg,#d9d6d0,#4a5566 70%,#3a4455);border-radius:150px 150px 0 0}
.quote blockquote{position:absolute;left:400px;top:130px;width:700px;text-align:center;font-size:28px;font-style:italic;line-height:36px;color:var(--ink)}
.quote .rule{position:absolute;left:600px;width:300px;height:1px;background:#e8a0a0}
.quote .who{position:absolute;left:400px;width:700px;text-align:center;font-size:14px}

/* info columns */
.info{left:0;top:2791px;width:1200px;height:261px;background:#f6f7f8}
.col{position:absolute;top:30px;width:330px;text-align:center;font-size:13px;color:var(--ink);line-height:19px}
.col h3{font-size:20px;font-weight:400;text-transform:uppercase;margin-bottom:24px}
.col .more{margin-top:18px;color:var(--muted)}
.col-sep{position:absolute;top:20px;width:1px;height:200px;background:var(--line)}
.staff{position:absolute;top:90px;width:110px;text-align:center;font-size:13px;line-height:17px}
.staff .pic{width:80px;height:80px;margin:0 auto 6px;background:linear-gradient(180deg,#e6dcd0,#8a97a8);border-radius:4px}
.staff small{display:block;font-size:11px;color:var(--muted)}
.chev{position:absolute;top:130px;font-size:26px;color:#999}

/* footer */
.footer{left:0;top:3052px;width:1200px;height:169px;background:#eceef0}
.footer .brand{left:108px;top:26px}
.footer .copy{position:absolute;left:108px;top:138px;font-size:11px;color:var(--muted)}
.contact{position:absolute;left:515px;top:50px;font-size:11px;color:var(--muted);line-height:24px}
.contact span{display:inline-block;width:12px;height:12px;border-radius:50%;background:#999;margin-right:8px;vertical-align:middle}
.social-foot{position:absolute;left:890px;top:62px;display:flex;gap:11px}
.social-foot span{width:40px;height:40px;border-radius:50%;background:#8f959b}
</style>
</head>
<body>

<div class="abs hero-photo" role="img" aria-label="Passenger jet flying toward the viewer against a bright blue sky"></div>
<div class="abs hero-arrow" style="left:0"><svg width="20" height="30" viewBox="0 0 20 30"><path d="M15 3 3 15l12 12" fill="none" stroke="#fff" stroke-width="4"/></svg></div>
<div class="abs hero-arrow" style="right:0"><svg width="20" height="30" viewBox="0 0 20 30"><path d="M5 3l12 12L5 27" fill="none" stroke="#fff" stroke-width="4"/></svg></div>

<header class="abs site-header">
  <div class="abs brand">
    <span class="brand-mark"></span>
    <div><div class="brand-name">Tarnwick Tours</div><div class="brand-tag">The professional's choice since 1974</div></div>
  </div>
  <div class="abs social-top"><span></span><span></span><span></span><span></span><span></span></div>
  <div class="abs search-top"></div>
  <div class="abs account"><span>SIGN IN</span><span>|</span><span>SIGN UP</span><span>|</span><span>MY ACCOUNT</span></div>
  <nav class="abs main-nav">
    <span class="active">Home</span><span>Travel Agencies</span><span>Religious &amp; Travel Group</span><span>Corporate Concierge</span><span>Niche Agencies</span><span>Destinations</span><span>About Tarnwick</span><span>Restricted Area</span>
  </nav>
</header>

<div class="abs tagline">
  <h1>MORE THAN JUST AIRLINE CONSOLIDATION</h1>
  <div class="stars">★★★★☆</div>
  <a>Checkout Our Reviews</a>
</div>

<form class="abs access">
  <div class="field">Enter Your Name</div>
  <div class="field">Enter Your E-mail address</div>
  <div class="go">Get Access Today!</div>
</form>

<section class="abs flight-search">
  <h2>FLIGHT SEARCH</h2>
  <div class="fs-input" style="left:30px;top:57px;width:252px">From To: (City or airport)<span class="caret"></span></div>
  <div class="fs-input" style="left:295px;top:57px;width:250px">Depart Date<span class="cal"></span></div>
  <div class="fs-input" style="left:570px;top:57px;width:150px">Time:<span class="caret"></span></div>
  <div class="fs-input" style="left:30px;top:97px;width:252px">To: (City or airport)<span class="caret"></span></div>
  <div class="fs-input" style="left:295px;top:97px;width:250px">Return Date<span class="cal"></span></div>
  <div class="fs-input" style="left:570px;top:97px;width:150px">Time:<span class="caret"></span></div>

  <div class="opt" style="left:745px;top:62px"><i class="on"></i>Economy</div>
  <div class="opt" style="left:845px;top:62px"><i></i>First/Business</div>
  <div class="opt" style="left:962px;top:62px"><i></i>Price</div>
  <div class="opt" style="left:745px;top:102px"><i></i>Schedule</div>
  <div class="opt" style="left:845px;top:102px"><i></i>Reward Travel</div>

  <div class="fs-input" style="left:30px;top:127px;width:150px;top:130px">Adults: 12+<span class="caret"></span></div>
  <div class="fs-input" style="left:30px;top:173px;width:150px">Children: 0-12<span class="caret"></span></div>
  <div class="opt" style="left:200px;top:138px"><i class="on"></i>Round trip</div>
  <div class="opt" style="left:200px;top:182px"><i></i>One Way</div>
  <div class="opt" style="left:315px;top:182px"><i></i>Multiple Destinations</div>

  <div class="fs-note" style="left:570px;top:140px">Find Lower Fare +/3 Days</div>
  <div class="fs-note" style="left:570px;top:168px">Search Nearby Airports</div>
  <div class="fs-input" style="left:785px;top:130px;width:248px">Offer Code (optional):</div>
  <div class="btn" style="left:865px;top:185px;width:168px;height:38px;font-size:15px">Search</div>
  <div class="fs-note" style="left:892px;top:232px;font-size:12px">Advanced Search</div>
</section>

<h2 class="section-title" style="top:712px">Airline Consolidator for Travel Agents</h2>

<div class="agent" style="left:40px;top:782px">
  <div class="icon"><svg width="40" height="40" viewBox="0 0 40 40"><path d="M4 20 20 6l16 14" fill="none" stroke="#2f6fb5" stroke-width="3"/><rect x="10" y="18" width="20" height="16" fill="#2f6fb5"/></svg></div>
  <h3>Home Based Travel Agents</h3>
  <div class="lead">Find your way to financial freedom!</div>
  <ul><li>• don't lose another client to the big guys</li><li>• get more referrals and more customers!</li></ul>
  <div class="more">earn more</div>
</div>
<div class="agent" style="left:450px;top:782px">
  <div class="icon"><svg width="44" height="30" viewBox="0 0 44 30"><rect x="2" y="6" width="40" height="16" rx="3" fill="#2f6fb5"/><circle cx="11" cy="25" r="4" fill="#2f6fb5"/><circle cx="33" cy="25" r="4" fill="#2f6fb5"/></svg></div>
  <h3>Small Travel Agencies</h3>
  <div class="lead">Accelerate your growth!</div>
  <ul><li>• don't lose another client to the big guys</li><li>• get more referrals and more customers!</li></ul>
  <div class="more">earn more</div>
</div>
<div class="agent" style="left:850px;top:782px">
  <div class="icon"><svg width="40" height="36" viewBox="0 0 40 36"><rect x="4" y="9" width="32" height="24" rx="3" fill="#2f6fb5"/><rect x="14" y="3" width="12" height="8" fill="none" stroke="#2f6fb5" stroke-width="3"/></svg></div>
  <h3>Corporate Travel Agencies</h3>
  <div class="lead">Earn &amp; retain higher value clients</div>
  <ul><li>• don't lose another client to the big guys</li><li>• get more referrals and more customers!</li></ul>
  <div class="more">earn more</div>
</div>
<div class="btn" style="left:122px;top:1055px;width:150px;height:46px;font-size:15px">Join Now</div>
<div class="btn" style="left:523px;top:1055px;width:150px;height:46px;font-size:15px">Join Now</div>
<div class="btn" style="left:907px;top:1055px;width:150px;height:46px;font-size:15px">Join Now</div>

<div class="divider" style="top:1133px"></div>
<h2 class="section-title" style="top:1187px">Trusted Members of</h2>
<div class="badge" style="left:305px" role="img" aria-label="Accreditation body badge"></div>
<div class="badge" style="left:540px" role="img" aria-label="Trade association badge"></div>
<div class="badge" style="left:760px" role="img" aria-label="Air transport association badge"></div>

<section class="abs corporate">
  <h2>Airline Consolidators for Businesses &amp; Corporations</h2>
  <div class="sub">Tired of travel headaches? Make business travel easy!</div>
  <div class="point" style="top:128px"><b>E</b>Excellent customer service, we staff over 200 agents and have locations in 6 major US cities</div>
  <div class="point" style="top:172px"><b>A</b>Always available ... buy in bulk &amp; save even more!</div>
  <div class="point" style="top:216px"><b>S</b>Save more by going direct to the consolidator!</div>
  <div class="point" style="top:260px"><b>Y</b>Your best interests are ours!</div>
  <div class="btn" style="left:402px;top:312px;width:418px;height:42px;font-size:15px">Experience the difference of Tarnwick!</div>
</section>
<div class="abs agent-photo" role="img" aria-label="Smiling customer service agent wearing a headset"></div>

<h2 class="section-title" style="top:1840px">Group Travel - Missionary Airfares, Hajj &amp; Umra Discounted Airfares</h2>
<div class="photo" style="left:145px;background:linear-gradient(135deg,#e8e3da,#c9a58a 55%,#6d6a4c)" role="img" aria-label="Smiling family with a young child"></div>
<div class="photo" style="left:636px;background:linear-gradient(180deg,#cfe0a8,#6f8f3a 45%,#4d6b2b)" role="img" aria-label="Large group of missionaries posing on grass"></div>
<div class="group" style="left:145px;top:2200px">
  <h3>Hajj Group Travel Rates</h3>
  <p>Lorem ipsum dolor sit amet, consectetur adipiscing elit. Nulla quam velit, vulputate eu pharetra nec, mattis ac neque</p>
</div>
<div class="group" style="left:636px;top:2200px">
  <h3>Missionary Travel</h3>
  <p>Lorem ipsum dolor sit amet, consectetur adipiscing elit. Nulla quam velit, vulputate eu pharetra nec, mattis ac neque</p>
</div>
<div class="btn" style="left:264px;top:2292px;width:200px;height:46px;font-size:15px">Contact Us Now</div>
<div class="btn" style="left:756px;top:2292px;width:200px;height:46px;font-size:15px">Contact Us Now</div>

<section class="abs quote">
  <div class="rule" style="top:112px"></div>
  <blockquote>"Great airfares are only the beginning, exceptional customer service and caring for our clients is what makes us so unique"</blockquote>
  <div class="rule" style="top:280px"></div>
  <div class="who" style="top:298px">Mr. Halvern</div>
  <div class="who" style="top:318px;font-size:11px">President &amp; CEO</div>
</section>
<div class="abs ceo-photo" role="img" aria-label="Company president in a suit, smiling"></div>

<section class="abs info">
  <div class="col" style="left:60px">
    <h3>Our History</h3>
    Lorem ipsum dolor sit amet, tetu adipiscing<br>elit, sed diam nonummy euismod<br>tincidunt ut<br>We're here for our clients!, Over 40 years in<br>Experience, 200 Employee ....
    <div class="more">Read more</div>
  </div>
  <div class="col-sep" style="left:395px"></div>
  <div class="col" style="left:420px">
    <h3>Our Divisions</h3>
    Lorem ipsum dolor sit amet, tetu adipiscing<br>elit, sed diam nonummy euismod<br>tincidunt ut<br><span style="color:var(--blue)">• The Airport • Airport Authority</span><br><span style="color:var(--blue)">• Air Cargo • Transfer</span>
    <div class="more">Read more</div>
  </div>
  <div class="col-sep" style="left:775px"></div>
  <div class="col" style="left:790px"><h3>Our Employees</h3></div>
  <div class="chev" style="left:758px">‹</div>
  <div class="chev" style="left:1090px">›</div>
  <div class="staff" style="left:815px"><div class="pic" role="img" aria-label="Staff portrait"></div>Dan Orlek<small>Manager</small><small>Read more</small></div>
  <div class="staff" style="left:955px"><div class="pic" role="img" aria-label="Staff portrait"></div>Mira Tolan<small>Secretary</small><small>Read more</small></div>
  <div class="abs" style="left:1090px;top:230px;font-size:11px;color:var(--muted)">See all</div>
</section>

<footer class="abs footer">
  <div class="abs brand">
    <span class="brand-mark"></span>
    <div><div class="brand-name">Tarnwick Tours</div><div class="brand-tag">The professional's choice since 1974</div></div>
  </div>
  <div class="copy">© 2016 &nbsp; PRIVACY POLICY</div>
  <div class="contact">
    <div><span></span>112 Harbor Lane, Suite 4, Albany, NY 12207</div>
    <div><span></span>1 - 555 - 123 - 4567</div>
    <div><span></span>info@tarnwicktours.com</div>
  </div>
  <div class="social-foot"><span></span><span></span><span></span><span></span><span></span><span></span></div>
</footer>

</body>
</html>
```